Brightfen Business Card Redesign & Logo Update

We need to update our business cards to something more modern and fresh. Brightfen can provide the current color schemes and old design examples, but welcome creativity in helping us with this redesign. PLEASE NOTE that we no longer utilize the "tree" and/or "leaf" imagery in our branding. If able would apprecaite an update on the quality of our "words only" logo in Ai. / PNG formats too.

Target Market(s)

Investors, landowners, corporate partners, contractors

Industry/Entity Type

Environmental Restoration & Conservation

Contact Information for Business Card

Logo, persons name, title, mailing address, phone and email, website url

Font styles to use
Other font styles liked:
• Merriweather

Requirements
Nice to have
• Logo, persons name, title, mailing address, phone and email, website url, but open to ideams
Should not have
• No all back backgrounds

```html
<!DOCTYPE html>
<html lang="en">
<head>
<meta charset="utf-8">
<title>Brightfen Business Card</title>
<link href="https://fonts.googleapis.com/css2?family=Oswald:wght@600;700&family=Roboto:wght@400;500&family=Poppins:wght@400&display=swap" rel="stylesheet">
<style>
  :root {
    --stage: #959393;
    --paper: #ffffff;
    --green: #137836;
    --orange: #ee7b00;
    --ink: #111111;
  }
  * { margin: 0; padding: 0; box-sizing: border-box; }
  html, body { width: 1075px; height: 1200px; overflow: hidden; }
  body { background: var(--stage); position: relative; font-family: "Roboto", sans-serif; }

  .card {
    position: absolute; left: 206px; width: 663px; height: 395px;
    background: var(--paper);
    box-shadow: 3px 3px 2px rgba(0,0,0,0.75);
    overflow: hidden;
  }
  .card--front { top: 187px; }
  .card--back { top: 637px; }

  .wordmark {
    font-family: "Oswald", sans-serif; font-weight: 700;
    color: var(--green); text-transform: uppercase;
    line-height: 1; letter-spacing: 1px;
  }
  .tagline {
    font-family: "Oswald", sans-serif; font-weight: 600;
    color: var(--ink); text-transform: uppercase;
    line-height: 1; letter-spacing: -0.3px;
  }

  .card--front .brand { position: absolute; right: 44px; top: 62px; text-align: center; }
  .card--front .wordmark { font-size: 76px; }
  .card--front .tagline { font-size: 22px; margin-top: 2px; }

  .holder { position: absolute; left: 35px; top: 216px; }
  .holder__name {
    font-family: "Oswald", sans-serif; font-weight: 600; font-size: 28px;
    line-height: 1; text-transform: uppercase; letter-spacing: -0.5px;
  }
  .holder__first { color: var(--orange); }
  .holder__last { color: var(--green); }
  .holder__title { font-size: 19px; color: var(--ink); margin-top: 5px; letter-spacing: 0.3px; }
  .holder__rule { position: absolute; left: 35px; top: 276px; width: 210px; height: 5px; background: var(--orange); }

  .contact-band {
    position: absolute; left: 0; top: 279px; width: 100%; height: 116px;
    background: var(--green); color: #fff;
  }
  .contact-list { position: absolute; left: 35px; top: 21px; list-style: none; }
  .contact-list li {
    display: flex; align-items: center; gap: 6px;
    font-size: 19px; line-height: 23.5px; letter-spacing: 0.2px;
  }
  .contact-list svg { width: 17px; height: 17px; flex: none; }
  .address {
    position: absolute; right: 40px; top: 50px; text-align: right;
    font-size: 19px; line-height: 24px; letter-spacing: 0.2px; font-style: normal;
  }

  .card--back .brand { position: absolute; left: 0; width: 100%; top: 148px; text-align: center; }
  .card--back .wordmark { font-size: 81px; }
  .card--back .tagline { font-size: 24px; margin-top: 2px; }
  .url-band {
    position: absolute; left: 0; bottom: 0; width: 100%; height: 45px;
    background: var(--orange); color: #fff; text-align: center;
    font-family: "Poppins", sans-serif; font-size: 19px; line-height: 45px; letter-spacing: 0.3px;
  }
</style>
</head>
<body>

<section class="card card--front">
  <div class="brand">
    <div class="wordmark">Brightfen</div>
    <div class="tagline">Environmental Credit Company</div>
  </div>

  <div class="holder">
    <div class="holder__name"><span class="holder__first">Daniel</span> <span class="holder__last">Hartley</span></div>
    <div class="holder__title">Managing Director</div>
  </div>
  <div class="holder__rule"></div>

  <div class="contact-band">
    <ul class="contact-list">
      <li>
        <svg viewBox="0 0 24 24" aria-hidden="true"><path fill="#ee7b00" d="M6.6 10.8a15.1 15.1 0 0 0 6.6 6.6l2.2-2.2a1 1 0 0 1 1-.25 11.4 11.4 0 0 0 3.6.57 1 1 0 0 1 1 1V20a1 1 0 0 1-1 1A17 17 0 0 1 3 4a1 1 0 0 1 1-1h3.5a1 1 0 0 1 1 1c0 1.25.2 2.45.57 3.57a1 1 0 0 1-.25 1z"/></svg>
        044-555 218 460
      </li>
      <li>
        <svg viewBox="0 0 24 24" aria-hidden="true"><rect x="2" y="5" width="20" height="14" fill="#ee7b00"/><path d="M2 5l10 8 10-8" fill="none" stroke="#137836" stroke-width="1.6"/></svg>
        info@brightfen.com
      </li>
      <li>
        <svg viewBox="0 0 24 24" aria-hidden="true"><g fill="none" stroke="#ee7b00" stroke-width="2"><circle cx="12" cy="12" r="9"/><ellipse cx="12" cy="12" rx="4" ry="9"/><path d="M3 12h18M5 7h14M5 17h14"/></g></svg>
        www.brightfen.com
      </li>
    </ul>
    <address class="address">421, Address line goes here<br>45452,Country Name</address>
  </div>
</section>

<section class="card card--back">
  <div class="brand">
    <div class="wordmark">Brightfen</div>
    <div class="tagline">Environmental Credit Company</div>
  </div>
  <div class="url-band">www.brightfen.com</div>
</section>

</body>
</html>
```